Business card por a urban DJ, up scale audience target

Need a sober design, modern, conservative colors but i can consider some options, y play rnb, hip hop, EDM and top40.

Business card for contact and personal info, double sided, use logo attrached please; im 42 so i need a card acording to my age an target audience.

Target Market(s)

Adult people, up scale audience

Industry/Entity Type

Music Download

Contact Information for Business Card

Cel (318) 4207265518 www.lumadrift.com

Requirements
Must have
• open mind
Nice to have
• open mind
Should not have
• DJ

```html
<!DOCTYPE html>
<html lang="en">
<head>
<meta charset="utf-8">
<title>Lumadrift Business Card</title>
<link rel="stylesheet" href="https://fonts.googleapis.com/css2?family=Lato:wght@400;700&display=swap">
<style>
  :root {
    --ink: #2b2b2b;
    --paper: #ffffff;
    --paper-shade: #f1f1f1;
    --backdrop: #e6e3de;
    --muted: #e4e4e4;
  }
  * { box-sizing: border-box; margin: 0; padding: 0; }
  html, body {
    width: 1200px;
    height: 900px;
    overflow: hidden;
    background: var(--backdrop);
    font-family: "Lato", Arial, sans-serif;
  }
  .canvas { position: relative; width: 1200px; height: 900px; }

  .card {
    position: absolute;
    width: 560px;
    height: 320px;
    border-radius: 3px;
    overflow: hidden;
    box-shadow: 0 10px 28px rgba(0,0,0,0.18);
  }

  .wordmark {
    font-weight: 700;
    letter-spacing: 6px;
    line-height: 1;
  }

  /* Back side */
  .card-back {
    left: 90px;
    top: 140px;
    background: var(--ink);
    display: flex;
    flex-direction: column;
    align-items: center;
    justify-content: center;
    gap: 24px;
  }
  .card-back .wordmark { color: var(--paper); font-size: 64px; }
  .back-url {
    color: var(--muted);
    font-size: 16px;
    font-weight: 700;
    letter-spacing: 0.5px;
  }

  /* Front side */
  .card-front {
    left: 550px;
    top: 440px;
    background: var(--paper);
  }
  .front-top {
    position: absolute;
    inset: 0 0 auto 0;
    height: 170px;
    background: linear-gradient(180deg, var(--paper) 0%, var(--paper-shade) 100%);
    display: flex;
    align-items: center;
    justify-content: flex-end;
    padding-right: 60px;
  }
  .front-top .wordmark { color: var(--ink); font-size: 64px; }
  .front-band {
    position: absolute;
    inset: 170px 0 0 0;
    background: var(--ink);
  }

  .person {
    position: absolute;
    left: 30px;
    top: 184px;
    width: 240px;
    text-align: right;
    color: var(--paper);
  }
  .person-name { font-size: 24px; font-weight: 400; }
  .person-role { font-size: 16px; color: var(--muted); margin-top: 2px; }
  .person-address { font-size: 17px; margin-top: 16px; line-height: 1.35; }

  .contacts {
    position: absolute;
    left: 300px;
    top: 186px;
    list-style: none;
    color: var(--paper);
    font-size: 15px;
  }
  .contacts li {
    display: flex;
    align-items: center;
    gap: 8px;
    height: 24px;
  }
  .contact-icon {
    width: 16px;
    height: 16px;
    flex: none;
  }
</style>
</head>
<body>
<main class="canvas">

  <section class="card card-back" aria-label="Card back">
    <p class="wordmark">LUMA</p>
    <p class="back-url">www.lumadrift.com</p>
  </section>

  <section class="card card-front" aria-label="Card front">
    <div class="front-top">
      <p class="wordmark">LUMA</p>
    </div>
    <div class="front-band"></div>

    <div class="person">
      <p class="person-name">John Smith</p>
      <p class="person-role">Managing Director</p>
      <p class="person-address">1234, Address GoesHere<br>Country, 12345</p>
    </div>

    <ul class="contacts">
      <li>
        <svg class="contact-icon" viewBox="0 0 16 16" aria-hidden="true">
          <rect width="16" height="16" rx="2" fill="#fff"/>
          <path d="M3 6.5c0-1.5 2.2-2.5 5-2.5s5 1 5 2.5v1h-2.5v-1.2h-5v1.2H3z M4.5 12l1.5-4h4l1.5 4z" fill="#2b2b2b"/>
        </svg>
        <span>123-456-7890</span>
      </li>
      <li>
        <svg class="contact-icon" viewBox="0 0 16 16" aria-hidden="true">
          <rect width="16" height="16" rx="2" fill="#fff"/>
          <rect x="3.5" y="3" width="9" height="10" rx="1" fill="none" stroke="#2b2b2b" stroke-width="1.4"/>
          <path d="M5.5 6h5M5.5 8.5h5M5.5 11h3" stroke="#2b2b2b" stroke-width="1.2"/>
        </svg>
        <span>123-456-7890</span>
      </li>
      <li>
        <svg class="contact-icon" viewBox="0 0 16 16" aria-hidden="true">
          <rect width="16" height="16" rx="2" fill="#fff"/>
          <rect x="3" y="4.5" width="10" height="7" fill="#2b2b2b"/>
          <path d="M3 4.5l5 4 5-4" fill="none" stroke="#fff" stroke-width="1"/>
        </svg>
        <span>info@youremail.com</span>
      </li>
      <li>
        <svg class="contact-icon" viewBox="0 0 16 16" aria-hidden="true">
          <rect width="16" height="16" rx="2" fill="#fff"/>
          <path d="M6.5 9.5l3-3M7 5.5l1-1a2 2 0 0 1 3 3l-1 1M9 10.5l-1 1a2 2 0 0 1-3-3l1-1" fill="none" stroke="#2b2b2b" stroke-width="1.4" stroke-linecap="round"/>
        </svg>
        <span>www.yourweb.com</span>
      </li>
    </ul>
  </section>

</main>
</body>
</html>
```